Family Owned and Operated Spray Foam Insulation Company needs a business card design

We're a new company based in the heart of Texas (Fort Worth). We spray foam insulation into residential houses, commercial buildings, metal buildings, etc. Spray foam insulation provides a huge reduction in energy/costs so that is what drives our market. We like the primary colors but are open to suggestions and are coming to the experts for some creativity. I'm attaching a picture of shirt mock up we have with KBL on the front to show what we were leaning towards as well as some business cards that I find striking and memorable. I'm looking for a card that is clean and professional with a bit of edge. Note: My computer won't pull up the color samples below for me to choose so it's in your hands.

Target Market(s)

Professional custom home builders, construction industry, home owners

Industry/Entity Type

Residential

Contact Information for Business Card

Name: Martin Kestrel (no title) Phone #: 817-555-0148, address: 4087 larkspur ave fort worth tx 76110, email: martin@kblinsulation.example, website: kblinsulation.example

Requirements
Must have
• We want the words KBL and Kestrel Spray Foam Insulation showcased on the card but hopefully on opposite sides
Should not have
• Any type of spray foam gun or splatter clip art

```html
<!DOCTYPE html>
<html lang="en">
<head>
<meta charset="utf-8">
<title>Kestrel Spray Foam Insulation – Business Card</title>
<link rel="stylesheet" href="https://fonts.googleapis.com/css2?family=Cinzel:wght@400&family=Oswald:wght@700&family=Arimo:wght@400&display=swap">
<style>
  :root {
    --backdrop: #e9e6e1;
    --card: #ffffff;
    --blue: #3b6ccf;
    --red: #e2403a;
    --faint: #edf1f7;
    --rule: #7a8fb8;
  }
  html, body {
    margin: 0;
    padding: 0;
    width: 1200px;
    height: 885px;
    overflow: hidden;
    background: var(--backdrop);
  }
  .canvas {
    position: relative;
    width: 1200px;
    height: 885px;
  }
  .card {
    position: absolute;
    width: 620px;
    height: 354px;
    background: var(--card);
    box-shadow: 0 10px 28px rgba(0,0,0,0.18);
    overflow: hidden;
  }
  .card--front { left: 40px; top: 70px; }
  .card--back  { left: 540px; top: 460px; }

  /* Front */
  .company-name {
    position: absolute;
    left: 40px;
    top: 150px;
    width: 300px;
    margin: 0;
    font-family: "Cinzel", serif;
    font-weight: 400;
    font-size: 25px;
    line-height: 1.25;
    letter-spacing: 1px;
    color: var(--blue);
    text-align: center;
  }
  .brand-mark {
    font-family: "Oswald", sans-serif;
    font-weight: 700;
    line-height: 1;
    color: var(--blue);
    letter-spacing: 2px;
  }
  .card--front .brand-mark {
    position: absolute;
    right: 44px;
    top: 26px;
    font-size: 112px;
  }
  .contact-row {
    position: absolute;
    left: 40px;
    right: 30px;
    bottom: 34px;
    display: flex;
    align-items: flex-end;
    gap: 16px;
    font-family: "Arimo", sans-serif;
    font-size: 15px;
    line-height: 1.3;
    color: var(--blue);
  }
  .contact-block { display: flex; flex-direction: column; white-space: nowrap; }
  .contact-divider {
    flex: none;
    width: 1px;
    height: 38px;
    background: var(--rule);
  }
  .person-name {
    font-family: "Oswald", sans-serif;
    font-weight: 700;
    font-size: 18px;
    color: var(--red);
    line-height: 1.1;
  }

  /* Back */
  .backdrop-mark {
    position: absolute;
    left: 0;
    right: 0;
    top: 50%;
    transform: translateY(-50%);
    text-align: center;
    font-size: 280px;
    color: var(--faint);
  }
  .back-lockup {
    position: absolute;
    inset: 0;
    display: flex;
    flex-direction: column;
    align-items: center;
    justify-content: center;
  }
  .back-lockup .brand-mark { font-size: 116px; }
  .tagline {
    margin: 8px 0 0;
    font-family: "Oswald", sans-serif;
    font-weight: 700;
    font-size: 24px;
    color: var(--blue);
  }
</style>
</head>
<body>
<main class="canvas">
  <section class="card card--front" aria-label="Card front">
    <h1 class="company-name">Kestrel Spray Foam<br>Insulation</h1>
    <div class="brand-mark">KBL</div>
    <div class="contact-row">
      <div class="contact-block">
        <span class="person-name">Martin Kestrel</span>
        <span>817-555-0148</span>
      </div>
      <span class="contact-divider"></span>
      <div class="contact-block">
        <span>martin@kblinsulation.example</span>
        <span>kblinsulation.example</span>
      </div>
      <span class="contact-divider"></span>
      <div class="contact-block">
        <span>4087 larkspur ave</span>
        <span>cedar hollow tx 76999</span>
      </div>
    </div>
  </section>

  <section class="card card--back" aria-label="Card back">
    <div class="backdrop-mark brand-mark" aria-hidden="true">KBL</div>
    <div class="back-lockup">
      <div class="brand-mark">KBL</div>
      <p class="tagline">Kestrel Spray Foam Insulation</p>
    </div>
  </section>
</main>
</body>
</html>
```